New, Schools ERP system needs a Brochure to go to the market

We are an IT company based in México City, over the past 3 years we have developed a solution for managing schools, finances, payments, and other administrative issues. Our model is Software as a Service, we re going to start a sales effort and we need a brochure for the sales people to leave it with the customer. The brochure is of the most importance since it will allow us to close the deal.
We would like a clean design, elegant and functional, the name of the system is tramo-k and we use colors like blue and green.
The design should present a modern and trustful service that could help the client to manage their business.
Updates

Hello everyone, we just uploaded a file with contents for the project, please check the files section in the project page.  Thanks & Regards

We upload a second file with a little introduction for the system, and the images of the system the you could use

Reason: Thanks to all designers that have participated, great work every one. We are still sending feedback and asking for some specific elements, so we are going to extend the deadline date by 3 days.

Target Market(s)

Target market is the directors, owners and financial decision makers, for the schools:
Gender, male or female
Ages: 30 to 50
Education level: college, postgraduates
Business oriented people

Industry/Entity Type

Business

Colors
0455a3

Requirements
Must have
• The design must have 4 sections or pages: system description, benefits, modules available and service model, the design also must present some screens of the system (2) regardless of the images that are related to the design.
The design must transmit easiness, organization, control, the benefits we are trying to offer to our users and clients.
Nice to have
• we look some multi pages brochures that are very well organized and easy to read and understand, we would like to see this kind of format.
As we have to print this brochure and the cost of high quality printing its high we would like a cost effective design.
Should not have
• The design should not be overcrowded or saturated.
Do not use font types that are difficult to read.

```html
<!DOCTYPE html>
<html lang="es">
<head>
<meta charset="utf-8">
<title>Tramo-k — Folleto</title>
<link rel="stylesheet" href="https://fonts.googleapis.com/css2?family=Arimo:wght@400;700&display=swap">
<style>
  :root {
    --brand-blue: #0455a3;
    --brand-green: #2ea84a;
    --sky: #8fd3e6;
    --sky-deep: #4fb3d3;
    --ink: #3a3f45;
    --paper: #ffffff;
    --backdrop: #e2e5e8;
    --rule-grey: #c9ced3;
    --accent-orange: #f39a1e;
    --accent-red: #d8352a;
  }
  * { box-sizing: border-box; margin: 0; padding: 0; }
  html, body { width: 1200px; height: 900px; overflow: hidden; }
  body {
    background: var(--backdrop);
    font-family: "Arimo", Arial, sans-serif;
    color: var(--ink);
    position: relative;
  }
  .spread {
    position: absolute; left: 40px; top: 180px;
    width: 1120px; height: 540px;
    display: flex;
    box-shadow: 0 18px 40px rgba(0,0,0,.18);
  }
  .page { position: relative; width: 560px; height: 540px; background: var(--paper); overflow: hidden; }
  .page--left { border-right: 1px solid #e6e8ea; }

  .photo-circle { position: absolute; border-radius: 50%; }
  .photo-ring { position: absolute; border-radius: 50%; border: 2px dotted var(--brand-blue); }

  /* Left page */
  .hero-band { position: absolute; left: 0; top: 0; }
  .photo--meeting { left: 330px; top: 70px; width: 140px; height: 140px;
    background: radial-gradient(circle at 45% 40%, #f2f2f2, #b9c2cb 60%, #6f7c88); }
  .ring--meeting { left: 320px; top: 60px; width: 160px; height: 160px; }
  .photo--keyboard { left: 478px; top: 82px; width: 96px; height: 96px;
    background: radial-gradient(circle at 40% 40%, #5b646e, #1f2327 70%); }

  .intro { position: absolute; left: 32px; top: 202px; width: 500px; }
  .section-title { color: var(--brand-green); font-weight: 700; font-size: 22px; letter-spacing: -.2px; line-height: 26px; }
  .lead { color: var(--brand-blue); font-weight: 700; font-size: 10.5px; line-height: 13px; margin-top: 5px; }
  .feature-list { list-style: none; margin-top: 8px; }
  .feature-list li {
    position: relative; padding-left: 13px;
    font-size: 9px; line-height: 11.5px; margin-bottom: 1px;
  }
  .feature-list li::before {
    content: ""; position: absolute; left: 0; top: 3px;
    width: 6px; height: 6px; border-radius: 50%; background: var(--brand-green);
  }

  /* Right page */
  .top-band { position: absolute; left: 0; top: 0; }
  .faq { position: absolute; left: 26px; top: 30px; list-style: none; }
  .faq li { display: flex; align-items: center; gap: 7px; font-size: 12px; font-weight: 700; color: var(--brand-blue); margin-bottom: 5px; }
  .faq .num { width: 15px; height: 15px; border-radius: 50%; color: #fff; font-size: 9px; display: flex; align-items: center; justify-content: center; }
  .num--1 { background: var(--brand-blue); }
  .num--2 { background: var(--accent-orange); }
  .num--3 { background: var(--accent-red); }
  .headline { position: absolute; left: 250px; top: 22px; width: 290px; color: #fff; font-weight: 700; font-size: 13px; line-height: 17px; }

  .photo--students { left: 40px; top: 150px; width: 150px; height: 150px;
    background: radial-gradient(circle at 50% 40%, #f3e3d4, #d7b49a 45%, #8fb7d8 80%); }
  .ring--students { left: 30px; top: 140px; width: 170px; height: 170px; }
  .photo--chip { left: 436px; top: 92px; width: 104px; height: 104px;
    background: radial-gradient(circle at 50% 50%, #c7e06a, #4f8f2e 55%, #12331f); }
  .ring--chip { left: 426px; top: 82px; width: 124px; height: 124px; }

  .service { position: absolute; left: 215px; top: 165px; width: 205px; }
  .service .section-title, .modules .section-title { font-size: 17px; line-height: 20px; }
  .body-copy { font-size: 8px; line-height: 11px; margin-top: 5px; color: var(--brand-blue); }

  .modules { position: absolute; left: 30px; top: 360px; width: 500px; }
  .modules .body-copy { font-weight: 700; }
  .module-list { list-style: none; margin-top: 6px; }
  .module-list li { position: relative; padding-left: 12px; font-size: 8.5px; line-height: 12px; margin-bottom: 2px; }
  .module-list li::before {
    content: ""; position: absolute; left: 0; top: 3px; width: 6px; height: 6px;
    border-radius: 50%; background: var(--brand-green);
  }
  .connector { position: absolute; left: 0; top: 0; pointer-events: none; }
</style>
</head>
<body>
<main class="spread">

  <section class="page page--left">
    <svg class="hero-band" width="560" height="200" viewBox="0 0 560 200">
      <defs>
        <linearGradient id="heroGrad" x1="0" y1="0" x2="1" y2="1">
          <stop offset="0" stop-color="#2f8ad0"/>
          <stop offset=".5" stop-color="#9fd2ee"/>
          <stop offset="1" stop-color="#dff0f9"/>
        </linearGradient>
      </defs>
      <path role="img" aria-label="Imagen de tecnología: globo terráqueo y piezas de rompecabezas en tonos azules"
            d="M0 0 H560 V140 Q300 130 0 172 Z" fill="url(#heroGrad)"/>
      <path d="M0 174 Q300 132 560 142" fill="none" stroke="var(--brand-green)" stroke-width="4"/>
      <path d="M0 182 Q300 140 560 150" fill="none" stroke="var(--rule-grey)" stroke-width="5"/>
    </svg>
    <div class="photo-ring ring--meeting"></div>
    <div class="photo-circle photo--meeting" role="img" aria-label="Fotografía de un equipo de trabajo en reunión de oficina"></div>
    <div class="photo-circle photo--keyboard" role="img" aria-label="Fotografía de un teclado con una tecla de gestión"></div>

    <div class="intro">
      <h1 class="section-title">Qué es Tramo-k</h1>
      <p class="lead">Tramo-k es una aplicación que permite controlar el proceso administrativo de una escuela, las definiciones necesarias para organizar a los alumnos y la administración de los pagos de cada estudiante</p>
      <ul class="feature-list">
        <li>Capacidad para múltiples escuelas, carreras, grados, ciclos, cajas y formas de pago</li>
        <li>Definición de estructuras de pago por escuela, carrera, grado y ciclo escolar. Colegiaturas, inscripciones y conceptos abiertos</li>
        <li>Definición y actualización de las estructuras de pagos por herencia para cada alumno, con la posibilidad de hacer ajustes individuales</li>
        <li>Definición y control automático de fechas límite de pago y cálculo de recargos</li>
        <li>Capacidad para integrar becas de cualquier porcentaje, prórrogas y convenios</li>
        <li>Formato de inscripción y tarjetón de pagos electrónicos</li>
        <li>Accesos basados en perfiles de usuario por usuario y contraseña</li>
        <li>Reportes varios predefinidos y reportes configurables por el usuario</li>
        <li>Facilita el control de pagos de las colegiaturas por medio de un control electrónico de pagos</li>
        <li>Fácil de usar y de integrar con los procesos diarios de la escuela</li>
        <li>Los padres pueden consultar en todo momento el estatus de los pagos de las colegiaturas de sus hijos y pueden solicitar el envío de recordatorios antes de la fecha límite</li>
        <li>Ofrece elementos de consulta y de control de primer nivel, incluso aplicación para dispositivos móviles</li>
        <li>Permite que la escuela tenga un portal dinámico, cuyo contenido se controla desde la escuela y es consultado de forma sistemática por los padres de familia</li>
        <li>Permite homogeneizar a un grupo de escuelas en base a una misma plataforma unificada</li>
      </ul>
    </div>
  </section>

  <section class="page page--right">
    <svg class="top-band" width="560" height="150" viewBox="0 0 560 150">
      <defs>
        <linearGradient id="skyGrad" x1="0" y1="0" x2="1" y2="0">
          <stop offset="0" stop-color="var(--sky)"/>
          <stop offset="1" stop-color="var(--sky-deep)"/>
        </linearGradient>
      </defs>
      <path d="M0 0 H560 V80 Q300 95 0 125 Z" fill="url(#skyGrad)"/>
      <path d="M0 128 Q300 98 560 84" fill="none" stroke="var(--brand-green)" stroke-width="4"/>
    </svg>
    <ol class="faq">
      <li><span class="num num--1">1</span>What is Tramo-k</li>
      <li><span class="num num--2">2</span>Where does it come from?</li>
      <li><span class="num num--3">3</span>Why do we use it?</li>
    </ol>
    <p class="headline">Administre y controle de manera sencilla y eficiente los pagos de sus alumnos, reduzca los retrasos y mejore la interacción con los padres de familia</p>

    <svg class="connector" width="560" height="540" viewBox="0 0 560 540">
      <path d="M175 165 Q300 125 426 148" fill="none" stroke="var(--brand-blue)" stroke-width="1.5" stroke-dasharray="2 4"/>
      <path d="M135 308 Q165 338 240 332" fill="none" stroke="var(--brand-blue)" stroke-width="1.5" stroke-dasharray="2 4"/>
    </svg>

    <div class="photo-ring ring--students"></div>
    <div class="photo-circle photo--students" role="img" aria-label="Fotografía de dos estudiantes sonrientes frente a una computadora portátil"></div>
    <div class="photo-ring ring--chip"></div>
    <div class="photo-circle photo--chip" role="img" aria-label="Ilustración de un circuito electrónico en tonos verdes"></div>

    <div class="service">
      <h2 class="section-title">Modelo de Servicio</h2>
      <p class="body-copy">Tramo-k se ofrece bajo un modelo de servicio en la nube, por lo que su escuela no necesita comprar servidores ni instalar programas. Usted solo se conecta desde cualquier navegador y paga una cuota mensual. Nuestro equipo se encarga del hospedaje, los respaldos diarios, la seguridad de la información y las actualizaciones del sistema, con soporte técnico disponible para su personal.</p>
    </div>

    <div class="modules">
      <h2 class="section-title">Módulos Disponibles</h2>
      <p class="body-copy">Tramo-k es un servicio modular que puede integrar diferentes módulos según las necesidades de su institución. Estos son los módulos disponibles hoy:</p>
      <ul class="module-list">
        <li>Control Académico: registro de carreras, grados, grupos, materias y calificaciones de cada ciclo escolar.</li>
        <li>Información Directiva: tablero con indicadores financieros y académicos para la toma de decisiones de los directivos.</li>
        <li>Facturación Electrónica: emisión automática de comprobantes fiscales para cada pago recibido por la escuela.</li>
      </ul>
    </div>
  </section>

</main>
</body>
</html>
```